7:40 Command Blueprint- A Handbook To Shape The Captain Others Could Trust

7:40 Command Blueprint
A Handbook To Shape The Captain Others Could Trust

It will be a 6 X 9 guide that is meant for people to keep with them with pages to fill out. See supporting pics for overall pillars that are discussed and form basis of the solution.

I will need a spine and back cover as well.

My blog and content: www.corvinmhale-example.com

Target Market(s)

Business professionals, senior emergency services people

Industry/Entity Type

Business Management

Font styles to use
Serif

Colors

Designer to choose colors to be used in the design.

Requirements
Must have
• Clean look, easily recognizable among other books. Front cover and back and spine. My picture on the back somewhere (corner maybe?!)
Nice to have
• Easily recognizeable
• NOTE: Graphic should read Today, Was I the Leader That I Would Want? I uploaded graphic that says ..."I Would've Wanted" which is incorrect.
Should not have
• Busy cover

```html
<!DOCTYPE html>
<html lang="en">
<head>
<meta charset="utf-8">
<title>7:40 Command Blueprint – Cover Spread</title>
<link rel="stylesheet" href="https://fonts.googleapis.com/css2?family=Oswald:wght@500;600&family=Arimo:wght@400&display=swap">
<style>
  :root {
    --stage: #000000;
    --paper: #f7f7f7;
    --paper-shade: #ececec;
    --accent-red: #c8161d;
    --ink: #1a1a1a;
    --rule: #333333;
    --pattern-light: #f4f4f4;
    --pattern-mid: #dcdcdc;
    --portrait: #050505;
  }
  * { margin: 0; padding: 0; box-sizing: border-box; }
  html, body {
    width: 1200px; height: 1200px; overflow: hidden;
    background: var(--stage);
  }
  .cover-spread {
    position: absolute; left: 48px; top: 228px;
    width: 1100px; height: 737px;
    background: linear-gradient(180deg, var(--paper) 0%, #ffffff 40%, var(--paper-shade) 100%);
    overflow: hidden;
    font-family: "Arimo", Arial, sans-serif;
    color: var(--ink);
  }
  .paper-pattern {
    position: absolute; left: 0; right: 0; bottom: 0; height: 160px;
    background: linear-gradient(180deg, rgba(255,255,255,0) 0%, var(--pattern-light) 35%, var(--pattern-mid) 100%);
  }

  /* Back cover */
  .back-cover { position: absolute; left: 0; top: 0; width: 501px; height: 100%; }
  .back-title {
    position: absolute; left: 35px; top: 24px;
    font-family: "Oswald", "Arial Narrow", sans-serif; font-weight: 500;
    font-size: 37px; letter-spacing: 0.5px; color: var(--accent-red);
    white-space: nowrap;
  }
  .back-copy {
    position: absolute; left: 35px; width: 442px;
    font-size: 13.6px; line-height: 16.3px; text-align: justify;
  }
  .back-copy.first { top: 80px; }
  .back-copy.second { top: 212px; }
  .back-rule {
    position: absolute; left: 35px; top: 442px; width: 442px;
    border-top: 1px solid var(--rule);
  }
  .author-portrait {
    position: absolute; left: 37px; top: 471px; width: 103px; height: 135px;
    background: var(--portrait);
  }
  .author-bio {
    position: absolute; left: 157px; top: 469px; width: 320px;
    font-size: 13.6px; line-height: 16.3px; text-align: justify;
  }
  .back-website {
    position: absolute; left: 35px; top: 702px;
    font-size: 13.5px;
  }

  /* Spine */
  .spine { position: absolute; left: 501px; top: 0; width: 89px; height: 100%; }
  .spine-title, .spine-author {
    position: absolute; left: 50%;
    transform-origin: 0 0; transform: rotate(90deg) translateY(-50%);
    white-space: nowrap;
  }
  .spine-title {
    top: 30px;
    font-family: "Oswald", "Arial Narrow", sans-serif; font-weight: 500;
    font-size: 33px; letter-spacing: 0.6px; color: var(--accent-red);
  }
  .spine-author {
    top: 566px;
    font-size: 18px; color: var(--ink);
  }

  /* Front cover */
  .front-cover { position: absolute; left: 590px; top: 0; width: 510px; height: 100%; }
  .front-title {
    position: absolute; left: 0; right: 0; top: 6px;
    text-align: center;
    font-family: "Oswald", "Arial Narrow", sans-serif; font-weight: 600;
    font-size: 96px; line-height: 108px; color: var(--accent-red);
    letter-spacing: 0.5px;
  }
  .front-subtitle {
    position: absolute; left: 45px; width: 435px; top: 331px;
    border-top: 1.5px solid var(--rule); border-bottom: 1.5px solid var(--rule);
    padding: 7px 0 6px;
    text-align: center; font-size: 17px; line-height: 20px;
    text-transform: uppercase;
  }
  .compass-art {
    position: absolute; left: 355px; top: 467px; width: 100px; height: 100px;
    border-radius: 50%;
    background: radial-gradient(circle, var(--accent-red) 0%, #b9b9b9 40%, #e9e9e9 70%, #9a9a9a 100%);
  }
  .front-author {
    position: absolute; left: 0; right: 0; top: 679px;
    text-align: center; font-size: 29px; letter-spacing: 0.3px;
  }
</style>
</head>
<body>
<main class="cover-spread">
  <div class="paper-pattern" role="img" aria-label="Soft pattern of folded paper diamonds along the bottom edge"></div>

  <section class="back-cover">
    <h2 class="back-title">7:40 COMMAND BLUEPRINT</h2>
    <p class="back-copy first">Lorem ipsum dolor sit amet, consectetur adipiscing elit, sed do eiusmod tempor incididunt ut labore et dolore magna aliqua. Ut enim ad minim veniam, quis nostrud exercitation ullamco laboris nisi ut aliquip ex ea commodo consequat. Duis aute irure dolor in reprehenderit in voluptate velit esse cillum dolore eu fugiat nulla pariatur. Excepteur sint occaecat cupidatat non proident, sunt in culpa qui officia deserunt mollit anim id est laborum.</p>
    <p class="back-copy second">Sed ut perspiciatis unde omnis iste natus error sit voluptatem accusantium doloremque laudantium, totam rem aperiam, eaque ipsa quae ab illo inventore veritatis et quasi architecto beatae vitae dicta sunt explicabo. Nemo enim ipsam voluptatem quia voluptas sit aspernatur aut odit aut fugit, sed quia consequuntur magni dolores eos qui ratione voluptatem sequi nesciunt. Neque porro quisquam est, qui dolorem ipsum quia dolor sit amet, consectetur, adipisci velit, sed quia non numquam eius modi tempora incidunt ut labore et dolore magnam aliquam quaerat voluptatem. Ut enim ad minima veniam, quis nostrum exercitationem ullam corporis suscipit laboriosam, nisi ut aliquid ex ea commodi consequatur? Quis autem vel eum iure reprehenderit qui in ea voluptate velit esse quam nihil molestiae consequatur, vel illum qui dolorem eum fugiat quo voluptas nulla pariatur?</p>
    <div class="back-rule"></div>
    <div class="author-portrait" role="img" aria-label="Author portrait"></div>
    <p class="author-bio">Lorem ipsum dolor sit amet, consectetur adipiscing elit, sed do eiusmod tempor incididunt ut labore et dolore magna aliqua. Ut enim ad minim veniam, quis nostrud exercitation ullamco laboris nisi ut aliquip ex ea commodo consequat. Duis aute irure dolor in reprehenderit in voluptate velit esse cillum dolore eu fugiat nulla pariatur. Excepteur sint occaecat cupidatat non proident, sunt in culpa qui officia deserunt mollit anim id est laborum.</p>
    <p class="back-website">www.corvinmhale-example.com</p>
  </section>

  <section class="spine">
    <p class="spine-title">7:40 COMMAND BLUEPRINT</p>
    <p class="spine-author">CORVIN M. HALE</p>
  </section>

  <section class="front-cover">
    <h1 class="front-title">7:40<br>COMMAND<br>BLUEPRINT</h1>
    <p class="front-subtitle">A practical and tactical handbook to shape<br>the captain others could trust</p>
    <div class="compass-art" role="img" aria-label="Compass with a red needle"></div>
    <p class="front-author">CORVIN M. HALE</p>
  </section>
</main>
</body>
</html>
```